established boer goat stud and dorper sheep stud need an updated look

I need a design to promote the boer goat stud and dorper sheep stud, so its clear and simple
Updates

Details for business card design Wirrabel Boers and Dorper Sheep Stud. I would like silhouette animal head or full body of a boer goat (not a dairy breed goat) and Dorper sheep. Contact: Maree Dalton +61 412578304 Sandra Pollock +61 438615027 Mooroopna North Victoria Australia Email: wirrabel5184@mailvane.com

Industry/Entity Type

Agriculture

Contact Information for Business Card

Wirrabel Boers and Dorper Sheep Stud Maree Dalton +61 412578304 Sandra Pollock +61 438615027 wirrabel5184@mailvane.com Wirrumba Victoria Australia

Colors
EE7325
F08F49
F5BC92
FAE3D3
FDF4ED

Requirements
Must have
• My Boer Goats and Dorper Sheep images see my photos

```html
<!DOCTYPE html>
<html lang="en">
<head>
<meta charset="utf-8">
<title>Wirrabel Boers &amp; Dorper Sheep Stud – Business Card</title>
<link rel="stylesheet" href="https://fonts.googleapis.com/css2?family=Oswald:wght@500&family=Arimo:wght@400;500&display=swap">
<style>
  :root {
    --page-bg: #e6e2dc;
    --card-bg: #f1f1ef;
    --card-edge: rgba(255,255,255,0.9);
    --ink: #1c1c1c;
    --band: #0d0d0d;
    --title: #efe3d2;
    --title-shade: #d8c4a8;
    --frame: #0a0a0a;
    --pasture: #6f8f3a;
    --fleece: #eae3d4;
  }
  * { box-sizing: border-box; margin: 0; padding: 0; }
  html, body { width: 1200px; height: 887px; overflow: hidden; }
  body {
    background: var(--page-bg);
    font-family: "Arimo", Arial, sans-serif;
    color: var(--ink);
  }
  .card {
    position: absolute;
    left: 108px;
    top: 176px;
    width: 984px;
    height: 535px;
    border-radius: 22px;
    background: var(--card-bg);
    border: 2px solid var(--card-edge);
    box-shadow: 0 10px 30px rgba(0,0,0,0.12);
    overflow: hidden;
  }
  .contacts {
    position: absolute;
    left: 50px;
    top: 64px;
    font-size: 24px;
    line-height: 38px;
    letter-spacing: 0.3px;
  }
  .contacts .name { font-weight: 500; text-transform: uppercase; }
  .title-band {
    position: absolute;
    left: 0;
    top: 203px;
    width: 560px;
    height: 130px;
    background: var(--band);
  }
  .title {
    position: absolute;
    right: 134px;
    top: 12px;
    text-align: right;
    font-family: "Oswald", "Arial Narrow", sans-serif;
    font-weight: 500;
    text-transform: uppercase;
    color: var(--title);
    letter-spacing: 2px;
    line-height: 1;
  }
  .title .line-main { display: block; font-size: 56px; }
  .title .line-sub { display: block; font-size: 42px; margin-top: 4px; color: var(--title-shade); }
  .details {
    position: absolute;
    left: 46px;
    top: 406px;
    font-size: 24px;
    line-height: 38px;
    letter-spacing: 0.3px;
  }
  .details .label { font-weight: 500; margin-right: 6px; }
  .photo-frame {
    position: absolute;
    left: 0;
    top: 0;
    width: 984px;
    height: 535px;
  }
</style>
</head>
<body>
  <div class="card">
    <div class="contacts">
      <div><span class="name">Maree Dalton</span> +61 412578304</div>
      <div><span class="name">Sandra Pollock</span> +61 438615027</div>
    </div>

    <div class="title-band">
      <h1 class="title">
        <span class="line-main">Wirrabel Boers</span>
        <span class="line-sub">&amp; Dorper Sheep Stud</span>
      </h1>
    </div>

    <div class="details">
      <div><span class="label">E :</span>wirrabel5184@mailvane.com</div>
      <div><span class="label">A :</span>Wirrumba Victoria Australia</div>
    </div>

    <svg class="photo-frame" viewBox="0 0 984 535" aria-hidden="false">
      <defs>
        <linearGradient id="pasture-tones" x1="0" y1="0" x2="1" y2="1">
          <stop offset="0" stop-color="#7a9a44"/>
          <stop offset="0.35" stop-color="#e6dfcf"/>
          <stop offset="0.7" stop-color="#efeae0"/>
          <stop offset="1" stop-color="#5f8232"/>
        </linearGradient>
      </defs>
      <circle class="photo-rim" cx="752" cy="268" r="278" fill="var(--frame)"/>
      <circle class="photo-area" cx="764" cy="268" r="270" fill="url(#pasture-tones)"
              role="img" aria-label="Photo of two Dorper sheep with black heads and white bodies standing on green pasture"/>
    </svg>
  </div>
</body>
</html>
```